Business Card for Coastal Tundrabridge Advisory

We need a business card for Coastal Tundrabridge Advisory. The company website address is provided below. The company logo is attached. We provide specialized permafrost services to the mining, transportation, and oil & gas industries. The card should be prepared for:
Matthias Korhonen, PhD.
Coastal Tundrabridge Advisory
PO Box 418259
Quillwater, Alaska 99642
Direct: +1-907-555-0143
Email: mkorhonen@tundrabridgeadvisory.example
Website: www.coastaltundrabridgeadvisory.example

```html
<!DOCTYPE html>
<html lang="en">
<head>
<meta charset="utf-8">
<title>Coastal Tundrabridge Advisory – Business Card</title>
<link href="https://fonts.googleapis.com/css2?family=Arimo:wght@400;700&display=swap" rel="stylesheet">
<style>
  :root {
    --page: #e4e4e4;
    --ink-dark: #10171f;
    --paper: #f7f7f7;
    --band: #5f5f5f;
    --light-text: #ffffff;
  }
  * { margin: 0; padding: 0; box-sizing: border-box; }
  html, body { width: 1200px; height: 1040px; overflow: hidden; }
  body {
    background: var(--page);
    font-family: "Arimo", Arial, sans-serif;
    position: relative;
  }
  .card {
    position: absolute;
    left: 278px;
    width: 644px;
    height: 368px;
    border-radius: 16px;
    overflow: hidden;
    box-shadow: 0 3px 6px rgba(0,0,0,0.25);
  }
  .card--front { top: 130px; background: var(--paper); }
  .card--back { top: 568px; background: var(--ink-dark); }

  .wave { position: absolute; inset: 0; width: 100%; height: 100%; }

  .brand-name {
    font-weight: 700;
    text-transform: uppercase;
    letter-spacing: 1.5px;
    line-height: 1.1;
  }
  .card--front .brand-name {
    position: absolute;
    left: 47px;
    top: 62px;
    font-size: 22px;
    color: var(--ink-dark);
  }

  .contact {
    position: absolute;
    right: 24px;
    color: var(--light-text);
    text-align: right;
    font-style: normal;
    font-size: 14px;
    line-height: 20px;
  }
  .contact__address { top: 170px; font-size: 15px; }
  .contact__lines { top: 220px; list-style: none; }
  .contact__lines li { display: flex; justify-content: flex-end; align-items: center; gap: 8px; white-space: nowrap; }
  .contact__lines svg { width: 12px; height: 12px; fill: var(--light-text); flex: none; }

  .person {
    position: absolute;
    right: 22px;
    top: 296px;
    text-align: right;
    color: var(--light-text);
  }
  .person__name { font-size: 22px; font-weight: 700; line-height: 26px; }
  .person__name small { font-size: 18px; }
  .person__title { font-size: 16px; line-height: 20px; }

  .card--back .brand-name {
    position: absolute;
    left: 0; right: 0;
    top: 138px;
    text-align: center;
    font-size: 34px;
    letter-spacing: 3px;
    color: var(--light-text);
  }
  .card--back .website {
    position: absolute;
    left: 0; right: 0;
    top: 318px;
    text-align: center;
    font-size: 15.5px;
    color: var(--light-text);
  }
</style>
</head>
<body>

<section class="card card--front">
  <svg class="wave" viewBox="0 0 801 458" preserveAspectRatio="none" aria-hidden="true">
    <path d="M0,284 C140,372 290,382 420,232 S690,52 801,60 L801,458 L0,458 Z" fill="var(--band)"/>
    <path d="M0,320 C140,402 290,402 420,252 S690,72 801,80 L801,458 L0,458 Z" fill="var(--ink-dark)"/>
    <path d="M0,320 C140,402 290,402 420,252 S690,72 801,80" fill="none" stroke="var(--paper)" stroke-width="4"/>
  </svg>

  <div class="brand-name">Coastal Tundrabridge<br>Advisory</div>

  <address class="contact contact__address">
    PO Box 418259<br>
    Quillwater, Alaska 99642
  </address>

  <ul class="contact contact__lines">
    <li>+1-907-555-0143
      <svg viewBox="0 0 24 24"><path d="M6.6 10.8a15.1 15.1 0 0 0 6.6 6.6l2.2-2.2c.3-.3.7-.4 1-.2 1.1.4 2.3.6 3.6.6.6 0 1 .4 1 1V20c0 .6-.4 1-1 1A17 17 0 0 1 3 4c0-.6.4-1 1-1h3.5c.6 0 1 .4 1 1 0 1.3.2 2.5.6 3.6.1.3 0 .7-.2 1z"/></svg>
    </li>
    <li>mkorhonen@tundrabridgeadvisory.example
      <svg viewBox="0 0 24 24"><path d="M2 6l10 7 10-7v13H2z"/><path d="M2 5h20l-10 7z"/></svg>
    </li>
    <li>www.coastaltundrabridgeadvisory.example
      <svg viewBox="0 0 24 24"><circle cx="12" cy="12" r="10"/><path d="M7 8l4 1-1 4 3 2-1 4-4-5zM15 5l3 3-2 2-2-2z" fill="var(--ink-dark)"/></svg>
    </li>
  </ul>

  <div class="person">
    <div class="person__name">Matthias Korhonen, <small>PhD.</small></div>
    <div class="person__title">President</div>
  </div>
</section>

<section class="card card--back">
  <div class="brand-name">Coastal Tundrabridge<br>Advisory</div>
  <div class="website">www.coastaltundrabridgeadvisory.example</div>
</section>

</body>
</html>
```